Defense Attorney Business Card Design Project/ Stationary

I am looking for a distinctive business card design for my solo law practice.
I practice criminal defense, both juvenile and adult, including DUI. I am a very experienced attorney with prior military experience. The design should convey a traditional, old school flair, but not be too stodgy or uptight. Some color. My logo should appear.
Updates

Project Deadline Extended Reason: I misunderstood how this project works and I was not prepared with my logo when this project ran the first time. Added Thursday, November 13, 2014

Project Deadline Extended
Reason: I was sent overseas on military duty last year, which interrupted this project. Thank you for your participation... I hope we can get this done this week! Thank you, Neil

Target Market(s)

Regular everyday people looking for strong, knowledgeable, authoritative representation while they are faced with criminal charges. Many have never been charged with a crime before. A reassuring air is therefore desired.

Industry/Entity Type

Business

Contact Information for Business Card

My information is:
Theodore M. Quill, Attorney at Law
785 Birch Avenue Suite 300
Oakland, California 94719
Tel: (510) 384-6125
Fax: (510) 391-7802
email: neilquilllaw@mailvine.example
web: www.neilquilllaw.example

Font styles to use
Serif
Sans Serif
Decorative

Colors
0255a3
ffffff

Requirements
Must have
• Sharp lines, bold elements. Conservative use of colors, such as deep blues, burgundy, grays for example.
• While my logo says "Neil Quill", it should be modified to show "Theodore M. Quill".
Should not have
• Cliche imagery such as scales of justice, gavels, Statue of Liberty, etc.

```html
<!DOCTYPE html>
<html lang="en">
<head>
<meta charset="utf-8">
<title>Neil Quill Law – Business Cards</title>
<link rel="stylesheet" href="https://fonts.googleapis.com/css2?family=Cinzel:wght@400;600&family=Alegreya:wght@400&display=swap">
<style>
  :root {
    --backdrop: #e6e4e1;
    --card-white: #f8f9fa;
    --card-grey: #7b7e81;
    --ink-grey: #7d7f82;
    --ink-dark: #5f6265;
    --line-grey: #8a8c8f;
    --white: #ffffff;
  }
  * { margin: 0; padding: 0; box-sizing: border-box; }
  html, body {
    width: 1200px; height: 1000px; overflow: hidden;
    background: var(--backdrop);
  }
  .sheet {
    position: relative; width: 1200px; height: 1000px;
    display: flex; flex-direction: column; align-items: center; justify-content: center;
    gap: 80px;
  }
  .card {
    position: relative; width: 630px; height: 360px;
    box-shadow: 0 6px 18px rgba(0,0,0,0.18);
    overflow: hidden;
  }

  /* Front: contact side */
  .card--contact { background: var(--card-white); }
  .rule { position: absolute; background: var(--line-grey); }
  .rule--horizontal { left: 0; right: 0; top: 168px; height: 2px; }
  .rule--top { left: 250px; top: 0; width: 2px; height: 168px; }
  .rule--bottom { left: 560px; top: 168px; width: 2px; bottom: 0; }
  .name-box {
    position: absolute; left: 290px; top: 146px;
    padding: 6px 18px; background: var(--card-white);
    border: 2px solid var(--line-grey);
    font-family: "Alegreya", serif; font-size: 27px; color: var(--ink-grey);
    white-space: nowrap;
  }
  .firm-lockup {
    position: absolute; left: 36px; top: 44px; width: 190px;
    font-family: "Cinzel", serif; color: var(--ink-dark);
  }
  .firm-lockup__row { display: flex; align-items: center; gap: 8px; }
  .firm-lockup__square { width: 12px; height: 12px; background: var(--ink-dark); }
  .firm-lockup__name { font-size: 21px; font-weight: 600; }
  .firm-lockup__tagline {
    margin-top: 6px; padding-top: 5px; border-top: 1.5px solid var(--ink-dark);
    font-size: 9.5px; letter-spacing: 0.5px;
  }
  .contact {
    position: absolute; left: 250px; top: 200px; width: 310px;
    text-align: center; font-family: "Alegreya", serif; color: var(--ink-grey);
  }
  .contact__address { font-size: 20px; line-height: 1.25; margin-bottom: 14px; }
  .contact__lines { font-size: 13.5px; line-height: 1.4; }

  /* Back: brand side */
  .card--brand { background: var(--card-grey); }
  .stripe { position: absolute; top: 0; bottom: 0; width: 2px; background: var(--white); }
  .stripe--l1 { left: 22px; } .stripe--l2 { left: 30px; }
  .stripe--r1 { right: 22px; } .stripe--r2 { right: 30px; }
  .brand-frame {
    position: absolute; left: 56px; right: 56px; top: 34px; bottom: 34px;
    border: 2px solid var(--white);
    display: flex; flex-direction: column; align-items: center; justify-content: center;
    color: var(--white); font-family: "Cinzel", serif; text-align: center;
  }
  .brand-frame__row { display: flex; align-items: center; gap: 14px; }
  .brand-frame__square { width: 22px; height: 22px; background: var(--white); }
  .brand-frame__name { font-size: 44px; font-weight: 400; letter-spacing: 1px; }
  .brand-frame__tagline {
    margin-top: 10px; padding-top: 8px; border-top: 1.5px solid var(--white);
    font-size: 16px; letter-spacing: 2px;
  }
</style>
</head>
<body>
<main class="sheet">
  <section class="card card--contact" aria-label="Contact side">
    <div class="rule rule--horizontal"></div>
    <div class="rule rule--top"></div>
    <div class="rule rule--bottom"></div>
    <div class="firm-lockup">
      <div class="firm-lockup__row">
        <span class="firm-lockup__name">Neil Quill Law</span>
        <span class="firm-lockup__square"></span>
      </div>
      <div class="firm-lockup__tagline">DUI - CRIMINAL DEFENSE - 420</div>
    </div>
    <div class="name-box">Neil Quill, Attorney</div>
    <div class="contact">
      <p class="contact__address">785 Birch Avenue Suite 300<br>Oakland, California 94719</p>
      <p class="contact__lines">
        Tel: (510) 384-6125<br>
        Fax: (510) 391-7802<br>
        Website: www.neilquilllaw.example<br>
        Email: neilquilllaw@mailvine.example
      </p>
    </div>
  </section>

  <section class="card card--brand" aria-label="Brand side">
    <div class="stripe stripe--l1"></div>
    <div class="stripe stripe--l2"></div>
    <div class="stripe stripe--r1"></div>
    <div class="stripe stripe--r2"></div>
    <div class="brand-frame">
      <div class="brand-frame__row">
        <span class="brand-frame__name">Neil Quill Law</span>
        <span class="brand-frame__square"></span>
      </div>
      <div class="brand-frame__tagline">DUI - CRIMINAL DEFENSE - 420</div>
    </div>
  </section>
</main>
</body>
</html>
```